Webdesign für Hersteller für Pack- und Palettieranlagen für den Getränke- und Lebensmittelbereich
Webdesign für Hersteller für Pack- und Palettieranlagen für den Getränke- und Lebensmittelbere..
Zielgruppe
Hersteller für Pack- und Palettieranlagen für den Getränke- und Lebensmittelbereich
Zielgruppe: Getränke- und Lebensmittelhersteller
Aufgabenstellung
die zukünftige Seite soll dynamischer und intuitiver werden
klare Strukturen, aber morderner als das jetztige Layout
Keine Kopie der alten Seite www.kolmatech.de!
Startseite soll aufgeräumter sein
Logo, Rufnummer, Mail, Social Media
Startseite mit großem Headerbild (Slider)

```html
<!DOCTYPE html>
<html lang="de">
<head>
<meta charset="utf-8">
<title>KOLMATECH Maschinenbau GmbH</title>
<link href="https://fonts.googleapis.com/css2?family=Inter:wght@400;500;600;700;800&display=swap" rel="stylesheet">
<style>
:root{
  --green:#6cbd2f;
  --graphite:#4a4a4a;
  --graphite-dark:#3c3c3c;
  --orange:#f07d1a;
  --light:#f1f1f1;
  --text:#333;
  --white:#fff;
}
*{margin:0;padding:0;box-sizing:border-box}
html,body{width:1200px;height:3475px;overflow:hidden}
body{font-family:"Inter",sans-serif;color:var(--text);background:var(--white);position:relative}
.abs{position:absolute}
.topbar{left:0;top:0;width:1200px;height:38px;background:var(--green);color:var(--white);font-size:13px;display:flex;align-items:center;padding:0 75px}
.topbar .contact{display:flex;gap:36px;align-items:center}
.topbar .contact span{display:flex;align-items:center;gap:10px}
.topbar .social{margin-left:auto;display:flex;gap:12px}
.topbar .social i{width:14px;height:14px;border-radius:50%;background:var(--white);display:block}
.nav{left:0;top:38px;width:1200px;height:56px;background:var(--graphite)}
.nav .brand{position:absolute;left:0;top:0;height:56px;width:243px;background:var(--white);clip-path:polygon(0 0,215px 0,243px 56px,0 56px);display:flex;align-items:center;padding-left:75px}
.brand-name{font-weight:700;font-size:17px;color:var(--graphite);line-height:1}
.nav ul{list-style:none;position:absolute;left:265px;top:0;height:56px;display:flex;align-items:center;gap:17px;color:var(--white);font-size:11.5px;font-weight:600}
.hero{left:0;top:94px;width:1200px;height:518px;background:linear-gradient(135deg,#8fa3b8 0%,#6e7c86 35%,#8a6e4f 65%,#4c5a66 100%)}
.hero-shade{left:0;top:94px;width:1200px;height:518px;background:linear-gradient(90deg,rgba(0,0,0,.45),rgba(0,0,0,.05))}
.hero-title{left:75px;top:166px;width:620px;font-size:41px;line-height:44px;font-weight:800;color:var(--white);white-space:nowrap}
.hero-lead{left:75px;top:378px;width:410px;font-size:10.5px;line-height:11px;font-weight:600;color:var(--white)}
.btn{display:inline-flex;align-items:center;justify-content:center;font-weight:600;font-size:13px;color:var(--white)}
.btn-green{background:var(--green)}
.btn-gray{background:var(--graphite)}
.hero-btn{left:75px;top:472px;width:144px;height:37px}
.dots{left:570px;top:585px;display:flex;gap:9px}
.dots i{width:7px;height:7px;background:var(--white);display:block}
.dots i:first-child{background:transparent;border:1px solid var(--white)}
.section-title{width:1200px;left:0;text-align:center;font-weight:700;font-size:25px;color:var(--graphite)}
.section-title::after{content:"";display:block;width:172px;height:2px;background:var(--green);margin:7px auto 0}
.title-orange::after{background:var(--orange)}
.products-bg{left:0;top:612px;width:1200px;height:1003px;background:var(--light)}
.card{width:518px;height:374px;overflow:hidden;box-shadow:0 8px 18px rgba(0,0,0,.12)}
.card .photo{position:absolute;inset:0}
.card .band{position:absolute;left:0;top:146px;width:100%;height:78px;background:var(--graphite);display:flex;align-items:center;justify-content:center;color:var(--green);font-weight:700;font-size:35px}
.card.active .photo{background:linear-gradient(160deg,#7cc548,#5fae2d)}
.card.active .band{background:transparent;color:var(--white)}
.card .more{position:absolute;left:0;width:100%;top:291px;text-align:center;color:var(--white);font-size:12.5px;font-weight:600}
.news-card{height:375px;top:1756px}
.news-card .txt{position:absolute;left:42px;bottom:34px;width:440px;color:var(--white)}
.news-card h3{font-size:27px;line-height:27px;font-weight:800;margin-bottom:14px}
.news-card p{font-size:10.5px;line-height:11px;font-weight:500}
.arrow{width:14px;height:14px}
.jobs{left:0;top:2205px;width:1200px;height:316px;background:linear-gradient(90deg,#62b327,#74c43a)}
.jobs-title{color:var(--white)}
.jobs-title::after{background:var(--white)}
.job{top:2323px;width:253px;height:155px;background:var(--white);text-align:center;padding-top:20px}
.job h4{font-size:14.5px;font-weight:600;color:var(--graphite)}
.job p{font-size:8.5px;line-height:9px;color:#666;margin:12px 36px 0}
.job .btn{width:143px;height:37px;margin-top:13px;font-size:12.5px}
.about-bg{left:0;top:2521px;width:1200px;height:375px;background:linear-gradient(180deg,#fafafa,#dcdcdc)}
.about-name{left:75px;top:2702px;width:520px;text-align:center;font-weight:700;font-size:30px;color:var(--graphite-dark)}
.about-text{left:607px;top:2656px;width:518px;font-size:10.5px;line-height:11.3px;color:#444}
.about-text p+p{margin-top:10px}
.contact-photo{left:607px;top:2896px;width:593px;height:412px;background:linear-gradient(180deg,#c9d3db 0%,#b8c2b0 40%,#6c8a4c 75%,#8d9097 100%)}
.contact-title{left:75px;top:2943px;font-size:25px;font-weight:700;color:var(--graphite)}
.field{position:absolute;font-size:11px;color:#444}
.field span{display:block;margin-top:5px;background:#eee;height:22px;line-height:22px;padding-left:8px;color:#aaa;font-size:10.5px}
.field span.filled{color:#333}
.message{left:75px;top:3126px;width:384px;height:81px;background:#eee;padding:9px 8px;font-size:10.5px;color:#aaa}
.send{left:75px;top:3231px;width:144px;height:37px;background:var(--orange);gap:10px}
.footer{left:0;top:3308px;width:1200px;height:167px;background:var(--graphite)}
.footer-head{position:absolute;top:3337px;font-size:11px;font-weight:700;color:var(--white)}
.footer-col{position:absolute;top:3358px;font-size:9.5px;line-height:20px;color:var(--white)}
.newsletter{position:absolute;left:951px;top:3364px;width:174px;height:27px;display:flex}
.newsletter span{flex:1;background:var(--white);color:#888;font-size:9px;line-height:27px;padding-left:10px}
.newsletter b{width:31px;background:var(--green);display:flex;align-items:center;justify-content:center}
.footer-line{left:0;top:3440px;width:1200px;height:1px;background:#5c5c5c}
.copyright{left:0;top:3450px;width:1200px;text-align:center;font-size:9.5px;font-weight:600;color:var(--white)}
</style>
</head>
<body>

<div class="abs topbar">
  <div class="contact">
    <span><svg width="13" height="13" viewBox="0 0 24 24"><path fill="#fff" d="M6.6 10.8a15 15 0 0 0 6.6 6.6l2.2-2.2c.3-.3.7-.4 1-.2 1.1.4 2.3.6 3.6.6.6 0 1 .4 1 1V20c0 .6-.4 1-1 1A17 17 0 0 1 3 4c0-.6.4-1 1-1h3.5c.6 0 1 .4 1 1 0 1.3.2 2.5.6 3.6.1.3 0 .7-.2 1z"/></svg>034511 / 420 - 0</span>
    <span><svg width="13" height="11" viewBox="0 0 24 18"><path fill="#fff" d="M0 0h24v18H0z"/><path d="M1 1l11 9 11-9" stroke="#6cbd2f" stroke-width="2" fill="none"/></svg>info@kolmatech.de</span>
  </div>
  <div class="social"><i></i><i></i><i></i><i></i></div>
</div>

<header class="abs nav">
  <div class="brand"><span class="brand-name">KOLMATECH</span></div>
  <ul>
    <li>UNTERNEHMEN</li><li>JOBS / KARRIERE</li><li>PALETTIERTECHNIK</li><li>PACKERTECHNIK</li><li>FÖRDERTECHNIK</li><li>ANLAGEN</li><li>GEBRAUCHTMASCHINEN</li><li>AKTUELLES</li>
  </ul>
</header>

<section>
  <div class="abs hero" role="img" aria-label="Produktionshalle mit Pack- und Palettieranlagen"></div>
  <div class="abs hero-shade"></div>
  <h1 class="abs hero-title">Hersteller Für Pack-<br>Und Palettieranlagen<br>Für Den Getränke-<br>Und Lebensmittelbereich</h1>
  <p class="abs hero-lead">Lorem Ipsum Dolor Sit Amet, Consectetur Adipiscing Elit, Sed Do Eiusmod Tempor Incididunt Ut Labore Et Dolore Magna Aliqua. Ut Enim Ad Minim Veniam, Quis Nostrud Exercitation Ullamco Laboris Nisi Ut Aliquip Ex Ea Commodo Consequat.</p>
  <a class="abs btn btn-green hero-btn">Mehr Erfahren</a>
  <div class="abs dots"><i></i><i></i><i></i><i></i></div>
</section>

<section>
  <div class="abs products-bg"></div>
  <h2 class="abs section-title" style="top:660px">PRODUKTE</h2>
  <div class="abs card" style="left:75px;top:745px">
    <div class="photo" role="img" aria-label="Palettierroboter in gelbem Schutzrahmen" style="background:linear-gradient(180deg,#d8d8d8,#b9a640 50%,#6a6a5a)"></div>
    <div class="band">PALETTIERTECHNIK</div>
  </div>
  <div class="abs card active" style="left:607px;top:745px">
    <div class="photo" role="img" aria-label="Packanlage mit Flaschen, grün eingefärbt"></div>
    <div class="band">PACKERTECHNIK</div>
    <div class="more">Mehr Erfahren &nbsp;›</div>
  </div>
  <div class="abs card" style="left:75px;top:1132px">
    <div class="photo" role="img" aria-label="Förderband mit Flaschen und roten Antrieben" style="background:linear-gradient(180deg,#c8ccd0,#9aa0a4 50%,#8a4a3a)"></div>
    <div class="band">FÖRDERTECHNIK</div>
  </div>
  <div class="abs card" style="left:607px;top:1132px">
    <div class="photo" role="img" aria-label="Gebrauchte Anlagen, Fässer und Getränkekisten" style="background:linear-gradient(180deg,#a89070,#8a7a6a 50%,#2e2e2e)"></div>
    <div class="band">GEBRAUCHTMASCHINEN</div>
  </div>
</section>

<section>
  <h2 class="abs section-title title-orange" style="top:1668px">AKTUELLES</h2>
  <div class="abs news-card" style="left:0;width:239px;background:linear-gradient(180deg,#9aa5b0,#b8a45a)" role="img" aria-label="Montage einer Palettieranlage"></div>
  <div class="abs news-card" style="left:341px;width:518px;background:linear-gradient(180deg,#6a5a4a,#7a4418 55%,#2a2420)" role="img" aria-label="Abfüllanlage mit braunen Flaschen">
    <div class="txt">
      <h3>Neue Abfüllanlage für<br>Brandel Limo</h3>
      <p>Der Traditionsreiche Limonadenhersteller Brandel Limo Aus Der Oberlausitz Investierte 2022/23 In Eine Neue Abfüllanlage. Federführend Beteiligt Bei Planung, Schnittstellenklärung Und Lieferung Der Anlage War Unser Unternehmen, In Zusammenarbeit Mit Weiteren Mittelständigen Firmen.</p>
    </div>
  </div>
  <div class="abs news-card" style="left:960px;width:240px;background:linear-gradient(180deg,#d8d8d4,#b8b4a8)" role="img" aria-label="Techniker an einer Anlage"></div>
  <svg class="abs arrow" style="left:283px;top:1935px" viewBox="0 0 14 14"><path d="M10 1L4 7l6 6" stroke="#f07d1a" stroke-width="2.4" fill="none"/></svg>
  <svg class="abs arrow" style="left:903px;top:1935px" viewBox="0 0 14 14"><path d="M4 1l6 6-6 6" stroke="#f07d1a" stroke-width="2.4" fill="none"/></svg>
</section>

<section>
  <div class="abs jobs"></div>
  <div class="abs" style="left:1025px;top:2181px;width:175px;height:340px;background:linear-gradient(180deg,#f2f2f2 0%,#d8c4b0 40%,#8a9aa8 100%);border-radius:80px 80px 0 0" role="img" aria-label="Ingenieur mit Schutzhelm"></div>
  <h2 class="abs section-title jobs-title" style="top:2251px">JOBS / KARRIERE</h2>
  <div class="abs job" style="left:164px"><h4>SPS-Programmierung</h4><p>Lorem Ipsum Dolor Sit Amet, Consectetur Adipiscing Elit, Sed Do Eiusmod Tempor Incididunt Ut Labore Et Dolore Magna Aliqua. Ut Enim Ad Min</p><a class="btn btn-green">Bewerben</a></div>
  <div class="abs job" style="left:474px"><h4>SPS-Programmierung</h4><p>Lorem Ipsum Dolor Sit Amet, Consectetur Adipiscing Elit, Sed Do Eiusmod Tempor Incididunt Ut Labore Et Dolore Magna Aliqua. Ut Enim Ad Min</p><a class="btn btn-gray">Bewerben</a></div>
  <div class="abs job" style="left:784px"><h4>SPS-Programmierung</h4><p>Lorem Ipsum Dolor Sit Amet, Consectetur Adipiscing Elit, Sed Do Eiusmod Tempor Incididunt Ut Labore Et Dolore Magna Aliqua. Ut Enim Ad Min</p><a class="btn btn-gray">Bewerben</a></div>
</section>

<section>
  <div class="abs about-bg" role="img" aria-label="Helle, verblasste Aufnahme einer Förderanlage"></div>
  <h2 class="abs section-title" style="top:2578px">UNTERNEHMEN</h2>
  <div class="abs about-name">KOLMATECH Maschinenbau GmbH</div>
  <div class="abs about-text">
    <p>Das Traditionsreiche Familienunternehmen Kolmatech Plant, Entwickelt Und Baut Pack- Und Palettieranlagen Für Den Getränke- Und Lebensmittelbereich. Mit Erfahrung Und Know-How Planen Und Konstruieren Wir Moderne Und Effiziente Anlagen, Die Optimal Auf Die Bedürfnisse Unserer Kunden Abgestimmt Sind.</p>
    <p>Wir Bieten Ihnen Individuelle Maschinen Und Anlagen Zur Abfüllung Und Verpackung, Sortier- Und Umpackanlagen Sowie Einen Umfassenden Rundum-Service An. Mit Unseren Weitläufigen Produktionsstätten Sind Wir In Der Lage, Die Vorarbeiten Der Montage Unter Unserem Dach Zu Erledigen, Sodass Der Zeitaufwand Für Den Aufbau Bei Ihnen Vor Ort Gering Ist.</p>
  </div>
  <a class="abs btn btn-gray" style="left:607px;top:2800px;width:143px;height:36px">Mehr Erfahren</a>
</section>

<section>
  <h2 class="abs contact-title">KONTAKT</h2>
  <div class="field" style="left:75px;top:2999px;width:175px">Vorname<span>Deine Vorname</span></div>
  <div class="field" style="left:284px;top:2999px;width:175px">Nachname<span>Deine Nachname</span></div>
  <div class="field" style="left:75px;top:3056px;width:175px">Email<span class="filled">info@kolmatech.de</span></div>
  <div class="field" style="left:284px;top:3056px;width:175px">Telefonnummer<span>Dein Telefonnummer</span></div>
  <div class="abs message">Schreibe deine Nachricht...</div>
  <a class="abs btn send"><svg width="15" height="15" viewBox="0 0 24 24"><path fill="#fff" d="M2 11L22 2l-9 20-2-8z"/></svg>Senden</a>
  <div class="abs contact-photo" role="img" aria-label="Luftaufnahme des Firmengeländes mit Halle und Parkplatz"></div>
</section>

<footer>
  <div class="abs footer"></div>
  <h5 class="footer-head" style="left:75px">KONTAKT</h5>
  <div class="footer-col" style="left:75px">KOLMATECH Maschinenbau GmbH<br>Am Werkring 12<br>04700 Talheim</div>
  <div class="footer-col" style="left:240px">034511 / 420 - 0<br>034511 / 420 - 14<br>info@kolmatech.de</div>
  <h5 class="footer-head" style="left:340px">QUICKLINKS</h5>
  <div class="footer-col" style="left:340px">Unternehmen<br>Jobs / Karriere<br>Palettiertechnik</div>
  <div class="footer-col" style="left:429px">Packertechnik<br>Fördertechnik<br>Anlagen</div>
  <div class="footer-col" style="left:517px">Gebrauchtmaschinen<br>Aktuelles</div>
  <h5 class="footer-head" style="left:649px">PRODUKTE</h5>
  <div class="footer-col" style="left:649px">PALETTIERTECHNIK<br>PACKERTECHNIK</div>
  <div class="footer-col" style="left:783px">FÖRDERTECHNIK<br>GEBRAUCHTMASCHINEN</div>
  <h5 class="footer-head" style="left:951px;font-size:9.5px">Abonnieren Sie den Newsletter</h5>
  <div class="newsletter"><span>Email</span><b><svg width="10" height="10" viewBox="0 0 10 10"><path d="M1 5h8M5 1l4 4-4 4" stroke="#fff" stroke-width="1.6" fill="none"/></svg></b></div>
  <div class="abs footer-line"></div>
  <div class="abs copyright">©2024. studio nordlicht All rights reserved</div>
</footer>

</body>
</html>
```